New Wrestling company needs a website

We need a website design for a new wrestling company in Australia that will be running 3-4 events per year. Wrestling company is Summit Grip Wrestling (SGW).

The design of the logo is in place and can be provided, and I have purchased the website domain.

A detailed description of the intent and purpose of this company can be provided.

The aim would be to have around 5 specific pages on SGW, with two standard “about” and “contact” pages. E.g.
- About SGW (focus and purpose of the company)
- SGW Events (specific focus on events run by SGW)
- SGW News (news and stories on wrestling’s across Oceania)
- SGW Media (where to watch SGW and our partners))
- SGW Partners and Sponsors (partner and affiliate information)
- SGW Power Rankings (top 10 ranked wrestlers from Oceania which is updated weekly)
- SGW fans (highlighting how to become part of SGW as a fan)
- Contact SGW
Updates

The logo design should now be included in the brief, please feel free to reach out to me directly if you can't access it or require any other information.

Target Market(s)

Wrestling Fans

Industry/Entity Type

Sport / Wrestling

Coding

Coded - Design and coding required

Number of Pages Required

5+ page

Requirements
Must have
• A Wrestling and or Sports feel to the website design

```html
<!DOCTYPE html>
<html lang="en">
<head>
<meta charset="utf-8">
<title>Summit Grip Wrestling</title>
<link href="https://fonts.googleapis.com/css2?family=Rajdhani:wght@600;700&family=Kumbh+Sans:wght@400;600;700&display=swap" rel="stylesheet">
<style>
:root{
  --blue:#2b7fd6;
  --blue-dark:#1f5fb3;
  --blue-light:#2ba4e2;
  --bg:#0b0b0d;
  --bg-deep:#000;
  --panel:#050506;
  --text:#fff;
  --muted:#d6d6d6;
}
*{margin:0;padding:0;box-sizing:border-box}
html,body{width:1200px;height:3886px;overflow:hidden}
body{background:var(--bg);color:var(--text);font-family:"Kumbh Sans",sans-serif;position:relative}
a{color:inherit;text-decoration:none}
.heading{font-family:"Rajdhani",sans-serif;font-weight:700;text-transform:uppercase;letter-spacing:.3px}
.accent{color:var(--blue)}
.btn{display:inline-flex;align-items:center;justify-content:center;border-radius:26px;background:linear-gradient(180deg,#3497ec,#1f5fb3);color:#fff;font-weight:700;font-size:14px;text-transform:uppercase;letter-spacing:.5px;box-shadow:0 0 0 3px rgba(43,127,214,.3)}
.abs{position:absolute}

/* header */
.site-header{position:absolute;top:0;left:0;width:1200px;height:90px;background:var(--bg);z-index:5}
.brand{position:absolute;left:112px;top:27px;display:flex;align-items:center;gap:10px;font-weight:700;font-size:32px;line-height:36px;color:var(--blue)}
.brand-dot{width:32px;height:32px;border-radius:50%;background:var(--blue)}
.main-nav a{position:absolute;top:0;height:90px;line-height:90px;font-size:14px;font-weight:700;text-transform:uppercase;color:#fff}
.main-nav .active{left:317px;width:82px;text-align:center;background:linear-gradient(180deg,#2b7fd6,#3a95ee)}
.social{position:absolute;display:flex;gap:12px;align-items:center}
.social span{width:18px;height:18px;border-radius:4px;border:2px solid #fff;display:block}
.social span:first-child{border-color:var(--blue)}

/* hero */
.hero{position:absolute;top:90px;left:0;width:1200px;height:700px;overflow:hidden}
.hero-photo{position:absolute;inset:0;background:
  radial-gradient(circle at 30% 2%,rgba(255,255,255,.55) 0,rgba(255,255,255,0) 90px),
  radial-gradient(circle at 96% 4%,rgba(255,255,255,.35) 0,rgba(255,255,255,0) 120px),
  radial-gradient(ellipse 120px 200px at 62% 30%,rgba(70,60,170,.55),rgba(0,0,0,0)),
  radial-gradient(ellipse 110px 170px at 70% 52%,rgba(150,30,40,.55),rgba(0,0,0,0)),
  radial-gradient(ellipse 260px 320px at 70% 48%,rgba(150,110,95,.45),rgba(0,0,0,0)),
  radial-gradient(ellipse at 70% 40%,#3a3e4c 0%,#1c1d26 40%,#09090b 78%)}
.hero-title{position:absolute;left:112px;top:186px;font-size:41px;line-height:46px}
.hero-sub{position:absolute;left:112px;top:240px;width:485px;font-size:16.5px;font-weight:600;line-height:26px}
.hero .btn{position:absolute;left:112px;top:317px;width:154px;height:47px}
.slider-arrow{position:absolute;width:33px;height:33px;border-radius:50%;background:#fff;display:flex;align-items:center;justify-content:center}

/* about */
.about-photo{left:113px;top:866px;width:410px;height:410px;border-radius:50%;background:
  radial-gradient(ellipse 70px 150px at 35% 55%,rgba(170,120,95,.7),rgba(0,0,0,0)),
  radial-gradient(ellipse 70px 150px at 68% 58%,rgba(140,95,75,.7),rgba(0,0,0,0)),
  radial-gradient(ellipse 200px 60px at 50% 92%,rgba(190,180,170,.55),rgba(0,0,0,0)),
  linear-gradient(180deg,#2b2d33,#4a4d55 45%,#5b6168 70%,#8a8680)}
.about-title{left:599px;top:885px;font-size:40px}
.about-text{left:599px;top:958px;width:490px;font-size:14.6px;line-height:26px;color:var(--muted);text-align:justify}
.about-text p+p{margin-top:16px}
.about .btn{left:599px;top:1197px;width:145px;height:50px}

/* events */
.events{position:absolute;top:1381px;left:0;width:1200px;height:505px;background:var(--bg-deep)}
.section-title{position:absolute;left:0;width:1200px;text-align:center;font-size:40px}
.event-card{position:absolute;top:136px;width:231px}
.event-photo{height:249px;border-radius:4px}
.event-name{margin-top:21px;text-align:center;color:var(--blue);font-weight:700;font-size:14px;letter-spacing:.3px}
.event-date{margin-top:7px;text-align:center;font-size:12px;font-weight:600}

/* media */
.media-card{position:absolute;top:2055px;width:302px}
.media-photo{height:206px;display:flex;align-items:center;justify-content:center}
.media-caption{margin-top:17px;text-align:center;font-size:16px;font-weight:600;line-height:26px}

/* partners */
.partners{position:absolute;top:2414px;left:0;width:1200px;height:360px;background:linear-gradient(180deg,#2ba4e2,#2276cf 55%,#1f55a8)}
.partner-badge{position:absolute;top:134px;width:167px;height:167px;border-radius:50%;background:#fff;box-shadow:0 4px 14px rgba(0,0,0,.18)}
.partners .arrow{position:absolute;top:202px}

/* news */
.news-photo{position:absolute;top:2950px;width:477px;height:261px}
.news-box{position:absolute;top:3211px;width:387px;height:167px;background:var(--panel);padding:20px 17px}
.news-date{display:flex;align-items:center;gap:10px;font-size:14px}
.news-title{margin-top:13px;font-size:17px;font-weight:700}
.news-text{margin-top:7px;font-size:14px;line-height:24px;color:var(--muted)}
.news-more{margin-top:7px;display:flex;align-items:center;gap:10px;font-size:14px;font-weight:700;color:var(--blue)}

/* footer */
.footer-col{position:absolute;top:3637px}
.footer-col h4{font-size:16px;font-weight:700;text-transform:uppercase;margin-bottom:22px}
.footer-col li{list-style:none;display:flex;align-items:center;gap:24px;font-size:14px;height:26.5px}
.contact-item{display:flex;gap:22px;font-size:14px;line-height:22px;margin-bottom:14px}
.footer-brand{left:955px;top:3712px;display:flex;align-items:center;gap:10px;font-weight:700;font-size:32px;color:var(--blue)}
.footer-bar{position:absolute;top:3829px;left:110px;width:980px;border-top:1px solid #222}
.copyright{position:absolute;top:3848px;left:0;width:1200px;text-align:center;font-size:12px}
</style>
</head>
<body>

<header class="site-header">
  <div class="brand"><span class="brand-dot"></span>SGW</div>
  <nav class="main-nav">
    <a class="active" href="#">Home</a>
    <a style="left:416px" href="#">About</a>
    <a style="left:507px" href="#">Power Rankings</a>
    <a style="left:687px" href="#">SGW Fans</a>
    <a style="left:805px" href="#">Contact</a>
  </nav>
  <div class="social" style="left:950px;top:36px" aria-label="Social links"><span></span><span></span><span></span><span></span><span></span></div>
</header>

<section class="hero">
  <div class="hero-photo" role="img" aria-label="Two wrestlers grappling under stage lights"></div>
  <svg class="abs" style="left:0;top:0" width="1200" height="700" viewBox="0 90 1200 700">
    <path d="M0 700 C120 600 320 610 560 690 C760 760 960 800 1200 676 L1200 790 L0 790 Z" fill="#0b0b0d"/>
    <path d="M0 710 C120 600 320 608 560 686 C760 756 960 790 1200 676 C960 806 760 778 560 706 C320 630 120 630 0 710 Z" fill="#2b7fd6"/>
  </svg>
  <h1 class="heading hero-title">Summit Grip Wrestling</h1>
  <p class="hero-sub">Sed ut perspiciatis unde omnis iste natus error sit volupt atem accusantium dolore laudantium.</p>
  <a class="btn" href="#">Get Started</a>
  <div class="slider-arrow" style="left:34px;top:268px"><svg width="12" height="12" viewBox="0 0 12 12"><path d="M8 2 4 6l4 4" stroke="#2b7fd6" stroke-width="2" fill="none"/></svg></div>
  <div class="slider-arrow" style="left:1129px;top:268px"><svg width="12" height="12" viewBox="0 0 12 12"><path d="M4 2l4 4-4 4" stroke="#2b7fd6" stroke-width="2" fill="none"/></svg></div>
</section>

<section class="about">
  <svg class="abs" style="left:100px;top:860px" width="440" height="430" viewBox="0 0 440 430"><path d="M150 24 A210 210 0 0 0 230 428" stroke="#2b7fd6" stroke-width="5" fill="none" stroke-linecap="round"/></svg>
  <div class="abs about-photo" role="img" aria-label="Two fighters sparring inside a training cage"></div>
  <h2 class="abs heading about-title">About <span class="accent">SGW</span></h2>
  <div class="abs about-text">
    <p>At vero eos et accusamus et iusto odio dignissimos ducimus qui blanditiis praesentium voluptatum deleniti atque corrupti quos dolores et quas molestias excepturi sint occaecati cupiditate non provident, similique sunt in culpa qui officiea.</p>
    <p>Deserunt mollitia animi, id est laborum et dolorum fuga. Et harum quidem rerum facilis est et expedita distinctio. Nam libero tempore, cum soluta nobis est eligendiea.</p>
  </div>
  <a class="abs btn" href="#">Learn More</a>
</section>

<section class="events">
  <h2 class="section-title heading" style="top:52px"><span class="accent">SGW</span> Events</h2>
  <div class="event-card" style="left:112px"><div class="event-photo" role="img" aria-label="Wrestlers grappling on a blue mat" style="background:radial-gradient(ellipse 60px 50px at 35% 55%,rgba(200,30,40,.75),rgba(0,0,0,0)),radial-gradient(ellipse 70px 60px at 65% 40%,rgba(200,200,210,.45),rgba(0,0,0,0)),linear-gradient(180deg,#1b1c21,#2a2c33 55%,#1f4fb0 75%,#173f96)"></div><div class="event-name">SED UT PERSPICIATIS</div><div class="event-date">11 JAN 2022</div></div>
  <div class="event-card" style="left:360px"><div class="event-photo" role="img" aria-label="Two boxers facing off in smoke" style="background:radial-gradient(ellipse 80px 120px at 50% 50%,rgba(160,120,100,.5),rgba(0,0,0,0)),radial-gradient(ellipse at 50% 80%,#5d7b92,#2b3a48 60%,#121820)"></div><div class="event-name">SED UT PERSPICIATIS</div><div class="event-date">11 JAN 2022</div></div>
  <div class="event-card" style="left:608px"><div class="event-photo" role="img" aria-label="Kickboxers training in a gym" style="background:radial-gradient(circle at 60% 20%,rgba(255,240,200,.5),rgba(0,0,0,0) 70px),radial-gradient(ellipse 50px 100px at 30% 55%,rgba(200,60,60,.45),rgba(0,0,0,0)),linear-gradient(180deg,#3e3d36,#2a2a26 55%,#55544c)"></div><div class="event-name">SED UT PERSPICIATIS</div><div class="event-date">11 JAN 2022</div></div>
  <div class="event-card" style="left:857px"><div class="event-photo" role="img" aria-label="Grapplers in blue and white uniforms" style="background:radial-gradient(ellipse 80px 70px at 62% 50%,rgba(40,80,200,.85),rgba(0,0,0,0)),radial-gradient(ellipse 60px 50px at 35% 45%,rgba(220,220,230,.6),rgba(0,0,0,0)),linear-gradient(180deg,#0c1324,#14254c 60%,#0a0f1a)"></div><div class="event-name">SED UT PERSPICIATIS</div><div class="event-date">11 JAN 2022</div></div>
</section>

<h2 class="section-title heading" style="top:1971px"><span class="accent">SGW</span> Media</h2>
<div class="media-card" style="left:112px"><div class="media-photo" role="img" aria-label="Video of wrestlers in red and blue" style="background:radial-gradient(ellipse 80px 70px at 30% 35%,rgba(190,40,45,.75),rgba(0,0,0,0)),radial-gradient(ellipse 90px 70px at 68% 55%,rgba(40,70,170,.85),rgba(0,0,0,0)),radial-gradient(ellipse 120px 80px at 50% 45%,rgba(170,120,95,.45),rgba(0,0,0,0)),#111216"><svg width="28" height="28" viewBox="0 0 28 28"><circle cx="14" cy="14" r="12" stroke="#fff" stroke-width="2" fill="rgba(0,0,0,.3)"/><path d="M11 8l8 6-8 6z" fill="#fff"/></svg></div><p class="media-caption">Sed ut pers atuiciatis undeom<br>lorum natus</p></div>
<div class="media-card" style="left:449px"><div class="media-photo" role="img" aria-label="Video of a boxer hitting focus mitts" style="background:radial-gradient(ellipse 60px 50px at 80% 25%,rgba(220,60,40,.8),rgba(0,0,0,0)),radial-gradient(ellipse 70px 110px at 35% 55%,rgba(150,105,80,.6),rgba(0,0,0,0)),linear-gradient(90deg,#2a2a2c,#19191b 60%,#2c2c2e)"><svg width="28" height="28" viewBox="0 0 28 28"><circle cx="14" cy="14" r="12" stroke="#fff" stroke-width="2" fill="rgba(0,0,0,.3)"/><path d="M11 8l8 6-8 6z" fill="#fff"/></svg></div><p class="media-caption">Sed ut pers atuiciatis undeom<br>lorum natus</p></div>
<div class="media-card" style="left:786px"><div class="media-photo" role="img" aria-label="Video of fighters grappling on a cage floor" style="background:radial-gradient(ellipse 60px 90px at 85% 30%,rgba(200,40,45,.75),rgba(0,0,0,0)),radial-gradient(ellipse 120px 50px at 45% 65%,rgba(60,60,70,.8),rgba(0,0,0,0)),linear-gradient(180deg,#26282e,#1a1c22 60%,#1e3a3e)"><svg width="28" height="28" viewBox="0 0 28 28"><circle cx="14" cy="14" r="12" stroke="#fff" stroke-width="2" fill="rgba(0,0,0,.3)"/><path d="M11 8l8 6-8 6z" fill="#fff"/></svg></div><p class="media-caption">Sed ut pers atuiciatis undeom<br>lorum natus</p></div>

<section class="partners">
  <h2 class="section-title heading" style="top:50px">SGW Partners</h2>
  <svg class="arrow" style="left:44px" width="30" height="32" viewBox="0 0 30 32"><path d="M18 4 6 16l12 12" stroke="#fff" stroke-width="4" fill="none"/></svg>
  <svg class="arrow" style="left:1126px" width="30" height="32" viewBox="0 0 30 32"><path d="M12 4l12 12-12 12" stroke="#fff" stroke-width="4" fill="none"/></svg>
  <div class="partner-badge" style="left:112px" aria-label="Partner"></div>
  <div class="partner-badge" style="left:314px" aria-label="Partner"></div>
  <div class="partner-badge" style="left:516px" aria-label="Partner"></div>
  <div class="partner-badge" style="left:718px" aria-label="Partner"></div>
  <div class="partner-badge" style="left:920px" aria-label="Partner"></div>
</section>

<h2 class="section-title heading" style="top:2860px">Latest <span class="accent">News</span></h2>
<div class="news-photo" style="left:112px;background:radial-gradient(ellipse 70px 90px at 52% 50%,rgba(200,50,50,.75),rgba(0,0,0,0)),radial-gradient(ellipse 60px 60px at 48% 75%,rgba(40,80,190,.7),rgba(0,0,0,0)),linear-gradient(180deg,#30343a,#6a7078 40%,#4b5158 75%,#2a2f36);border-bottom:10px solid #1f62b8" role="img" aria-label="Wrestlers in red and blue gear in a gym"></div>
<div class="news-photo" style="left:611px;background:radial-gradient(circle at 30% 12%,rgba(220,235,255,.6),rgba(0,0,0,0) 45px),radial-gradient(circle at 70% 10%,rgba(220,235,255,.55),rgba(0,0,0,0) 45px),radial-gradient(ellipse 90px 80px at 50% 65%,rgba(190,130,60,.5),rgba(0,0,0,0)),radial-gradient(ellipse at 50% 25%,#4a6a8a,#1c2a3a 55%,#0c121a)" role="img" aria-label="Two fighters in an arena cage"></div>
<article class="news-box" style="left:201px">
  <div class="news-date"><svg width="13" height="13" viewBox="0 0 13 13"><rect x="1" y="2" width="11" height="10" rx="1" stroke="#2b7fd6" stroke-width="1.5" fill="none"/><path d="M1 5h11M4 0v3M9 0v3" stroke="#2b7fd6" stroke-width="1.5"/></svg>11 Jan 2022</div>
  <h3 class="news-title">At vero eos et accusamus etea</h3>
  <p class="news-text">Lorem ipsum dolor sit amet, consectetur adipisc<br>ing elit, sed do eiusmod temporea.</p>
  <a class="news-more" href="#">Read More <svg width="13" height="13" viewBox="0 0 13 13"><circle cx="6.5" cy="6.5" r="5.5" stroke="#2b7fd6" stroke-width="1.6" fill="none"/><path d="M5 4l3 2.5L5 9" stroke="#2b7fd6" stroke-width="1.6" fill="none"/></svg></a>
</article>
<article class="news-box" style="left:700px">
  <div class="news-date"><svg width="13" height="13" viewBox="0 0 13 13"><rect x="1" y="2" width="11" height="10" rx="1" stroke="#2b7fd6" stroke-width="1.5" fill="none"/><path d="M1 5h11M4 0v3M9 0v3" stroke="#2b7fd6" stroke-width="1.5"/></svg>11 Jan 2022</div>
  <h3 class="news-title">At vero eos et accusamus etea</h3>
  <p class="news-text">Lorem ipsum dolor sit amet, consectetur adipisc<br>ing elit, sed do eiusmod temporea.</p>
  <a class="news-more" href="#">Read More <svg width="13" height="13" viewBox="0 0 13 13"><circle cx="6.5" cy="6.5" r="5.5" stroke="#2b7fd6" stroke-width="1.6" fill="none"/><path d="M5 4l3 2.5L5 9" stroke="#2b7fd6" stroke-width="1.6" fill="none"/></svg></a>
</article>

<footer>
  <svg class="abs" style="left:0;top:3440px" width="1200" height="210" viewBox="0 0 1200 210">
    <path d="M0 130 C150 40 360 30 620 110 C820 175 1000 180 1200 100 L1200 210 L0 210 Z" fill="#050506"/>
    <path d="M0 140 C150 38 360 24 620 100 C820 162 1000 166 1200 80 L1200 100 C1000 186 820 186 620 116 C360 40 150 56 0 148 Z" fill="#2b7fd6"/>
  </svg>
  <div class="abs" style="left:0;top:3600px;width:1200px;height:286px;background:#050506"></div>
  <div class="footer-col" style="left:110px">
    <h4>Quick Links</h4>
    <ul>
      <li><svg width="13" height="13" viewBox="0 0 13 13"><circle cx="6.5" cy="6.5" r="5.5" stroke="#2b7fd6" stroke-width="1.6" fill="none"/><path d="M5 4l3 2.5L5 9" stroke="#2b7fd6" stroke-width="1.6" fill="none"/></svg>Home</li>
      <li><svg width="13" height="13" viewBox="0 0 13 13"><circle cx="6.5" cy="6.5" r="5.5" stroke="#2b7fd6" stroke-width="1.6" fill="none"/><path d="M5 4l3 2.5L5 9" stroke="#2b7fd6" stroke-width="1.6" fill="none"/></svg>About</li>
      <li><svg width="13" height="13" viewBox="0 0 13 13"><circle cx="6.5" cy="6.5" r="5.5" stroke="#2b7fd6" stroke-width="1.6" fill="none"/><path d="M5 4l3 2.5L5 9" stroke="#2b7fd6" stroke-width="1.6" fill="none"/></svg>Power Rankings</li>
      <li><svg width="13" height="13" viewBox="0 0 13 13"><circle cx="6.5" cy="6.5" r="5.5" stroke="#2b7fd6" stroke-width="1.6" fill="none"/><path d="M5 4l3 2.5L5 9" stroke="#2b7fd6" stroke-width="1.6" fill="none"/></svg>SGW fans</li>
      <li><svg width="13" height="13" viewBox="0 0 13 13"><circle cx="6.5" cy="6.5" r="5.5" stroke="#2b7fd6" stroke-width="1.6" fill="none"/><path d="M5 4l3 2.5L5 9" stroke="#2b7fd6" stroke-width="1.6" fill="none"/></svg>Contact</li>
    </ul>
  </div>
  <div class="footer-col" style="left:352px">
    <h4>Other Links</h4>
    <ul>
      <li><svg width="13" height="13" viewBox="0 0 13 13"><circle cx="6.5" cy="6.5" r="5.5" stroke="#2b7fd6" stroke-width="1.6" fill="none"/><path d="M5 4l3 2.5L5 9" stroke="#2b7fd6" stroke-width="1.6" fill="none"/></svg>Privacy Policy</li>
      <li><svg width="13" height="13" viewBox="0 0 13 13"><circle cx="6.5" cy="6.5" r="5.5" stroke="#2b7fd6" stroke-width="1.6" fill="none"/><path d="M5 4l3 2.5L5 9" stroke="#2b7fd6" stroke-width="1.6" fill="none"/></svg>Terms Of Use</li>
      <li><svg width="13" height="13" viewBox="0 0 13 13"><circle cx="6.5" cy="6.5" r="5.5" stroke="#2b7fd6" stroke-width="1.6" fill="none"/><path d="M5 4l3 2.5L5 9" stroke="#2b7fd6" stroke-width="1.6" fill="none"/></svg>Legal Support</li>
    </ul>
  </div>
  <div class="footer-col" style="left:598px">
    <h4>Contact</h4>
    <div class="contact-item"><svg width="12" height="16" viewBox="0 0 12 16"><path d="M6 1a5 5 0 0 1 5 5c0 4-5 9-5 9S1 10 1 6a5 5 0 0 1 5-5z" fill="#2b7fd6"/><circle cx="6" cy="6" r="2" fill="#050506"/></svg><span>465, Lorum Ipsum Dolore<br>Australia</span></div>
    <div class="contact-item"><svg width="13" height="13" viewBox="0 0 13 13"><path d="M2 1h3l1 3-2 1.5a8 8 0 0 0 3.5 3.5L9 7l3 1v3c0 1-1 1.5-2 1.5C5 12.5.5 8 .5 3 .5 2 1 1 2 1z" fill="#2b7fd6"/></svg><span>+61 (02) 5550 0123</span></div>
    <div class="contact-item"><svg width="14" height="12" viewBox="0 0 14 12"><rect x="0" y="1" width="14" height="10" rx="1" fill="#2b7fd6"/><path d="M1 2l6 5 6-5" stroke="#050506" stroke-width="1.4" fill="none"/></svg><span>info@summitgripwrestling.com</span></div>
  </div>
  <div class="abs footer-brand"><span class="brand-dot"></span>SGW</div>
  <div class="footer-bar"></div>
  <p class="copyright">© 2022 <strong>SUMMIT GRIP WRESTLING</strong>. ALL RIGHTS RESERVED</p>
  <div class="social" style="left:950px;top:3845px" aria-label="Social links"><span></span><span></span><span></span><span></span><span></span></div>
</footer>

</body>
</html>
```